Velvet Circle club

We are looking to redesign the user interface of our mobile app “Velvet Circle”, which is the official rewards program for our luxury casino brand, Kestrane Harbour.
Our goal is to give the app a more elegant, premium, and user-friendly design that reflects the exclusivity of our brand and the luxury experience we offer our VIP clientele.
What We Need:
A complete UI design for the app’s main screens, including:
Splash Screen
01 Login / Signup Screen
02 Home Dashboard
Buttons -
Home / my card / my wallet / my booking / my host
My wallet / my offer / lucky game / my taxi / entertainment / online
03 Profile screen
04 My wallet
05 My offer
06Packages
07 My booking
08 My host
09 My card
we attached our privies app all the screen for you reference
Inspiration:
Think of luxury brands like Dunmore-Vale, Corvix Onyx, or high-end lifestyle apps. Clean interfaces, classy animations, and a sense of exclusivity are key.
We’re excited to see fresh, innovative takes that elevate the app to a truly world-class luxury experience for our users.
Thank you!
Casino

```html
<!DOCTYPE html>
<html lang="en">
<head>
<meta charset="utf-8">
<title>Velvet Circle – App Screens</title>
<link href="https://fonts.googleapis.com/css2?family=Oswald:wght@500;600&family=Arimo:wght@400;700&display=swap" rel="stylesheet">
<style>
  :root{
    --page:#ffffff;
    --screen:#16130f;
    --screen-deep:#0d0b09;
    --header:#221e1a;
    --gold:#f0a21f;
    --gold-soft:#c98a23;
    --text:#ffffff;
    --muted:#d9d4cc;
    --nav:#1e1b18;
    --nav-active:#e9a33a;
  }
  *{box-sizing:border-box;margin:0;padding:0}
  html,body{width:1200px;height:823px;overflow:hidden;background:var(--page)}
  body{font-family:"Arimo",Arial,sans-serif;color:var(--text)}
  .stage{position:absolute;left:0;top:0;width:1376px;height:943px;transform:scale(.8721);transform-origin:0 0}
  .screen{position:absolute;top:65px;width:375px;height:812px;overflow:hidden;
    background:linear-gradient(180deg,var(--screen) 0%,var(--screen-deep) 100%)}
  .screen--login{left:72px}
  .screen--home{left:500px}
  .screen--redeem{left:927px}

  .app-header{position:absolute;left:0;top:0;width:375px;height:80px}
  .status{position:absolute;top:10px;left:20px;right:20px;display:flex;justify-content:space-between;font-size:13px;font-weight:700}
  .status-icons{display:flex;gap:4px;align-items:center}
  .brand{position:absolute;top:38px;left:0;width:375px;text-align:center;display:flex;flex-direction:column;align-items:center;gap:2px}
  .brand-dot{width:9px;height:9px;border-radius:50%;background:#d8322a}
  .brand-name{font-size:8px;font-weight:700;color:var(--gold);letter-spacing:.3px}

  .title{position:absolute;left:0;width:375px;text-align:center;font-family:"Oswald",Impact,sans-serif;font-weight:600;color:var(--gold);font-size:27px;letter-spacing:.3px;line-height:1}
  .copy{position:absolute;left:20px;width:335px;text-align:center;font-size:12.5px;line-height:20px;color:var(--text)}
  .btn{position:absolute;left:50%;transform:translateX(-50%);height:36px;border:2px solid var(--gold);border-radius:18px;display:flex;align-items:center;justify-content:center;font-size:13px;font-weight:700;color:var(--text)}
  .photo{position:absolute;left:0;width:375px}

  .round-btn{position:absolute;width:26px;height:26px;border-radius:50%;background:#3a3129;display:flex;align-items:center;justify-content:center}

  .tile{position:absolute;width:159px;height:138px;border-radius:6px;border-bottom:3px solid var(--gold-soft)}
  .tile-label{position:absolute;width:159px;text-align:center;font-size:12px;font-weight:700;color:var(--muted)}

  .step-title{position:absolute;left:0;width:375px;text-align:center;font-size:14px;font-weight:700;color:var(--gold)}
  .step-text{position:absolute;left:22px;width:331px;text-align:center;font-size:11px;line-height:17px;color:var(--text)}
  .rule{position:absolute;left:20px;width:335px;height:1px;background:var(--gold-soft)}
  .subtitle{position:absolute;left:0;width:375px;text-align:center;font-size:14px;color:var(--text)}

  .tabbar{position:absolute;left:0;bottom:0;width:375px;height:67px;background:var(--nav);display:flex;border-radius:14px 14px 0 0}
  .tab{display:flex;flex-direction:column;align-items:center;justify-content:center;gap:6px;font-size:12px;color:var(--muted)}
  .tab--active{background:var(--nav-active);color:#3a2a12}
  .tab svg{width:22px;height:22px}
</style>
</head>
<body>
<svg width="0" height="0" style="position:absolute">
  <defs>
    <symbol id="ic-home" viewBox="0 0 24 24"><path d="M12 3 2 12h3v8h5v-5h4v5h5v-8h3z" fill="#f0a21f"/></symbol>
    <symbol id="ic-user" viewBox="0 0 24 24"><circle cx="12" cy="12" r="10" fill="none" stroke="#1b1510" stroke-width="2"/><circle cx="12" cy="10" r="3.5" fill="#1b1510"/><path d="M5.5 18.5c1.5-3 3.8-4 6.5-4s5 1 6.5 4" fill="#1b1510"/></symbol>
    <symbol id="ic-wallet" viewBox="0 0 24 24"><rect x="2" y="7" width="20" height="13" rx="2" fill="#f0a21f"/><path d="M8 7V5h8v2" fill="none" stroke="#f0a21f" stroke-width="2"/><rect x="2" y="12" width="20" height="1.5" fill="#1e1b18"/></symbol>
    <symbol id="ic-cal" viewBox="0 0 24 24"><rect x="3" y="5" width="18" height="16" rx="2" fill="none" stroke="#f0a21f" stroke-width="2"/><path d="M3 9h18M8 3v4M16 3v4M7 13h2M11 13h2M15 13h2M7 17h2M11 17h2M15 17h2" stroke="#f0a21f" stroke-width="2"/></symbol>
    <symbol id="ic-gem" viewBox="0 0 24 24"><path d="M6 4h12l4 5-10 12L2 9z M2 9h20 M9 4l3 17 3-17" fill="none" stroke="#f0a21f" stroke-width="1.8" stroke-linejoin="round"/></symbol>
    <symbol id="ic-bell" viewBox="0 0 24 24"><path d="M12 3a6 6 0 0 0-6 6v5l-2 3h16l-2-3V9a6 6 0 0 0-6-6zM10 19a2 2 0 0 0 4 0z" fill="#f0a21f"/></symbol>
    <symbol id="ic-header" viewBox="0 0 375 80"><path d="M0 0h375v10c-35 50-90 68-187 68S35 60 0 10z" fill="#221e1a"/><path d="M0 10c35 50 90 68 188 68s152-18 187-68" fill="none" stroke="#c98a23" stroke-width="2"/></symbol>
    <symbol id="ic-status" viewBox="0 0 60 12"><rect x="0" y="7" width="3" height="4" fill="#fff"/><rect x="4" y="5" width="3" height="6" fill="#fff"/><rect x="8" y="3" width="3" height="8" fill="#fff"/><rect x="12" y="1" width="3" height="10" fill="#fff"/><path d="M19 4a9 9 0 0 1 12 0l-2 2a6 6 0 0 0-8 0zM22 7a4 4 0 0 1 6 0l-3 3z" fill="#fff"/><rect x="36" y="1" width="20" height="10" rx="3" fill="none" stroke="#fff"/><rect x="38" y="3" width="16" height="6" rx="1.5" fill="#fff"/></symbol>
  </defs>
</svg>

<div class="stage">

  <!-- Login -->
  <section class="screen screen--login">
    <div class="app-header">
      <svg width="375" height="80"><use href="#ic-header"/></svg>
      <div class="status"><span>12:00 ➚</span><svg width="60" height="12"><use href="#ic-status"/></svg></div>
      <div class="brand"><span class="brand-dot"></span><span class="brand-name">VELVET CIRCLE</span></div>
    </div>
    <h1 class="title" style="top:118px">MEMBER LOGIN</h1>
    <p class="copy" style="top:158px">Now You Can Enjoy At The Excitement of The Casing Right At Your Fingertios</p>
    <div class="btn" style="top:219px;width:115px">SIGN IN</div>
    <h2 class="title" style="top:287px">NEW MEMBER LOGIN</h2>
    <p class="copy" style="top:327px">If You Are a Firstome User, Please Go Through The Sign Up</p>
    <div class="btn" style="top:368px;width:115px">SIGN UP</div>
    <h2 class="title" style="top:445px">OR</h2>
    <p class="copy" style="top:485px">If You are With A Temporary ID: Sign In Here</p>
    <div class="btn" style="top:526px;width:190px">TEMPORARY SIGN IN</div>
    <div class="photo" role="img" aria-label="Excited man celebrating in a casino among glowing slot machines" style="top:605px;height:207px;background:radial-gradient(ellipse at 50% 45%,#e8a344 0%,#8a4e1c 40%,#2a1a10 75%,#16130f 100%)"></div>
  </section>

  <!-- Home -->
  <section class="screen screen--home">
    <div class="app-header">
      <svg width="375" height="80"><use href="#ic-header"/></svg>
      <div class="status"><span>12:00 ➚</span><svg width="60" height="12"><use href="#ic-status"/></svg></div>
      <div class="brand"><span class="brand-dot"></span><span class="brand-name">VELVET CIRCLE</span></div>
    </div>
    <h1 class="title" style="top:99px">HOME</h1>
    <div class="round-btn" style="left:292px;top:100px"><svg width="16" height="16"><use href="#ic-bell"/></svg></div>
    <div class="round-btn" style="left:327px;top:100px"><svg width="14" height="14" viewBox="0 0 14 14"><path d="M2 3h10M2 7h10M2 11h10" stroke="#f0a21f" stroke-width="2"/></svg></div>

    <div class="tile" role="img" aria-label="Wallet holding banknotes" style="left:20px;top:157px;background:linear-gradient(160deg,#c9414a,#e9e2d2 45%,#2a2624 70%)"></div>
    <div class="tile" role="img" aria-label="Man cheering while looking at his phone" style="left:194px;top:157px;background:linear-gradient(160deg,#f2f1ee,#cfc9c0 50%,#6a5a4c)"></div>
    <div class="tile-label" style="left:20px;top:313px">MY WOLLET</div>
    <div class="tile-label" style="left:194px;top:313px">MY OFFER</div>

    <div class="tile" role="img" aria-label="Man celebrating in front of colourful lights" style="left:20px;top:348px;background:linear-gradient(135deg,#3a7bd0,#d84a3a 45%,#f3a03a 75%,#2a1a20)"></div>
    <div class="tile" role="img" aria-label="Taxi roof sign on a city street at dusk" style="left:194px;top:348px;background:linear-gradient(180deg,#d9a27a,#6e7a8c 45%,#3a4250 80%,#8fb0d4)"></div>
    <div class="tile-label" style="left:20px;top:504px">LUCKY GAME</div>
    <div class="tile-label" style="left:194px;top:504px">MY TAXI</div>

    <div class="tile" role="img" aria-label="Group of friends playing video games under neon lights" style="left:20px;top:539px;background:linear-gradient(135deg,#2a3a9a,#7a3ab0 50%,#1a1a3a)"></div>
    <div class="tile" role="img" aria-label="Smiling woman using her phone at home" style="left:194px;top:539px;background:linear-gradient(135deg,#f4f0ea,#e0b060 55%,#b07a2a)"></div>
    <div class="tile-label" style="left:20px;top:695px">ENTERTAINMENT</div>
    <div class="tile-label" style="left:194px;top:695px">ONLINE</div>

    <nav class="tabbar">
      <div class="tab" style="width:66px"><svg><use href="#ic-home"/></svg>Home</div>
      <div class="tab tab--active" style="width:67px"><svg><use href="#ic-user"/></svg>My Card</div>
      <div class="tab" style="width:76px"><svg><use href="#ic-wallet"/></svg>My Wallet</div>
      <div class="tab" style="width:89px"><svg><use href="#ic-cal"/></svg>My Booking</div>
      <div class="tab" style="width:77px"><svg><use href="#ic-gem"/></svg>My Host</div>
    </nav>
  </section>

  <!-- How to redeem -->
  <section class="screen screen--redeem">
    <div class="app-header">
      <svg width="375" height="80"><use href="#ic-header"/></svg>
      <div class="status"><span>12:00 ➚</span><svg width="60" height="12"><use href="#ic-status"/></svg></div>
      <div class="brand"><span class="brand-dot"></span><span class="brand-name">VELVET CIRCLE</span></div>
    </div>
    <div class="round-btn" style="left:21px;top:100px"><svg width="12" height="12" viewBox="0 0 12 12"><path d="M8 2 4 6l4 4" fill="none" stroke="#f0a21f" stroke-width="1.6"/></svg></div>
    <h1 class="title" style="top:99px">HOW TO REDEEM</h1>
    <div class="round-btn" style="left:325px;top:100px"><svg width="16" height="16"><use href="#ic-bell"/></svg></div>
    <p class="subtitle" style="top:140px">How To Redeem Your Vouchers</p>

    <h3 class="step-title" style="top:176px">STEP 01</h3>
    <p class="step-text" style="top:198px">Select the preferred Partner you want t redeem your voucher at</p>
    <div class="rule" style="top:227px"></div>

    <h3 class="step-title" style="top:240px">STEP 02</h3>
    <p class="step-text" style="top:262px">Presant your Kestrane Harbour voucher at time of payment by showing the voucher and number appearing on your mobile</p>
    <div class="rule" style="top:312px"></div>

    <h3 class="step-title" style="top:326px">STEP 03</h3>
    <p class="step-text" style="top:348px">Indicate the number and value of the voucher you want to pay with</p>
    <div class="rule" style="top:375px"></div>

    <h3 class="step-title" style="top:390px">STEP 03</h3>
    <p class="step-text" style="top:412px">You will receive a message to your app indicating a successful transaction</p>
    <div class="rule" style="top:461px"></div>

    <h3 class="step-title" style="top:476px">STEP 03</h3>
    <p class="step-text" style="top:498px">The transaction voucher will get deleted from your Voucher</p>

    <div class="photo" role="img" aria-label="Excited couple celebrating a win on a phone" style="top:544px;height:201px;background:linear-gradient(120deg,#5a6a80 0%,#c9b29a 35%,#b5562e 65%,#3a2a24 100%)"></div>

    <nav class="tabbar">
      <div class="tab" style="width:66px"><svg><use href="#ic-home"/></svg>Home</div>
      <div class="tab tab--active" style="width:67px"><svg><use href="#ic-user"/></svg>My Card</div>
      <div class="tab" style="width:76px"><svg><use href="#ic-wallet"/></svg>My Wallet</div>
      <div class="tab" style="width:89px"><svg><use href="#ic-cal"/></svg>My Booking</div>
      <div class="tab" style="width:77px"><svg><use href="#ic-gem"/></svg>My Host</div>
    </nav>
  </section>

</div>
</body>
</html>
```